MRT Property - Business Cards

Looking for a business card & general letterhead, signage etc design for our new logo.

Colours:
000a20
0056a2
00b5ef
0088ce
68cef2

Fonts:
Poppins
Karla

Please keep look and feel of new brand - example in the zip package I sent.

```html
<!DOCTYPE html>
<html lang="en">
<head>
<meta charset="utf-8">
<title>MRT Property – Business Cards</title>
<link href="https://fonts.googleapis.com/css2?family=Poppins:wght@400;500;600;700&display=swap" rel="stylesheet">
<style>
  :root {
    --ink: #000a20;
    --navy: #0056a2;
    --deep: #0d4f9e;
    --sky: #00b5ef;
    --mid: #0088ce;
    --pale: #68cef2;
    --paper: #ffffff;
    --stage: #222222;
  }
  * { box-sizing: border-box; margin: 0; padding: 0; }
  html, body { width: 1200px; height: 780px; overflow: hidden; background: var(--stage); }
  body { font-family: "Poppins", sans-serif; color: var(--ink); }
  .canvas { position: relative; width: 1200px; height: 780px; }

  .card {
    position: absolute;
    top: 235px;
    width: 540px;
    height: 310px;
    overflow: hidden;
    box-shadow: 0 18px 40px rgba(0,0,0,.55);
  }
  .card--front { left: 45px; background: var(--paper); }
  .card--back { left: 615px; }

  .front-waves { position: absolute; left: 0; top: 0; width: 540px; height: 310px; }

  .brand {
    position: absolute;
    left: 150px; top: 42px;
    display: flex; align-items: center; gap: 10px;
  }
  .brand__dot { width: 22px; height: 22px; border-radius: 50%; background: var(--pale); }
  .brand__name { font-size: 36px; font-weight: 700; color: var(--navy); letter-spacing: -0.5px; line-height: 1; }

  .contacts { position: absolute; left: 22px; top: 112px; list-style: none; }
  .contacts li { display: flex; align-items: center; gap: 7px; font-size: 11.5px; line-height: 19px; font-weight: 500; }
  .contacts svg { width: 11px; height: 11px; flex: none; }

  .person { position: absolute; right: 40px; top: 166px; text-align: right; }
  .person__name { font-size: 27px; font-weight: 700; line-height: 1.05; letter-spacing: -0.3px; }
  .person__first { color: var(--navy); }
  .person__last { color: var(--pale); font-weight: 400; }
  .person__role { font-size: 13px; font-weight: 600; margin-top: 2px; }
  .side-tab { position: absolute; right: 0; top: 176px; width: 16px; height: 58px; background: var(--pale); }

  .address { position: absolute; right: 40px; bottom: 22px; text-align: right; font-size: 12.5px; line-height: 18px; font-weight: 500; font-style: normal; }

  .back-field {
    position: absolute; inset: 0;
    background: radial-gradient(ellipse at 100% 0%, #2e8fd8 0%, var(--deep) 45%, #0b4794 100%);
  }
  .back-brand {
    position: absolute; left: 340px; top: 212px;
    display: flex; align-items: center; gap: 5px;
  }
  .back-brand__dot { width: 9px; height: 9px; border-radius: 50%; background: var(--pale); }
  .back-brand__name { font-size: 15px; font-weight: 700; color: var(--paper); line-height: 1; }
</style>
</head>
<body>
<main class="canvas">

  <section class="card card--front" aria-label="Business card front">
    <svg class="front-waves" viewBox="0 0 540 310" aria-hidden="true">
      <path d="M0 198 C 130 214, 260 255, 350 310 L 0 310 Z" fill="var(--pale)"/>
      <path d="M0 209 C 125 226, 245 265, 326 310 L 0 310 Z" fill="var(--paper)"/>
      <path d="M0 215 C 120 233, 238 270, 314 310 L 0 310 Z" fill="var(--navy)"/>
    </svg>

    <div class="brand">
      <span class="brand__dot"></span>
      <span class="brand__name">MRT Property</span>
    </div>

    <ul class="contacts">
      <li>
        <svg viewBox="0 0 24 24" aria-hidden="true"><path fill="var(--mid)" d="M6.6 10.8a15 15 0 0 0 6.6 6.6l2.2-2.2c.3-.3.7-.4 1-.2 1.1.4 2.3.6 3.6.6.6 0 1 .4 1 1V20c0 .6-.4 1-1 1A17 17 0 0 1 3 4c0-.6.4-1 1-1h3.5c.6 0 1 .4 1 1 0 1.3.2 2.5.6 3.6.1.3 0 .7-.2 1z"/></svg>
        +61 2 9000 4821
      </li>
      <li>
        <svg viewBox="0 0 24 24" aria-hidden="true"><circle cx="12" cy="12" r="9" fill="none" stroke="var(--mid)" stroke-width="2.2"/><path d="M3 12h18M12 3c3 3 3 15 0 18M12 3c-3 3-3 15 0 18" fill="none" stroke="var(--mid)" stroke-width="1.8"/></svg>
        www.mrtproperty.com.au
      </li>
      <li>
        <svg viewBox="0 0 24 24" aria-hidden="true"><rect x="2" y="5" width="20" height="14" rx="2" fill="var(--mid)"/><path d="M3 6l9 7 9-7" fill="none" stroke="#fff" stroke-width="1.8"/></svg>
        info@mrtproperty.com.au
      </li>
    </ul>

    <div class="person">
      <p class="person__name"><span class="person__first">Callum</span> <span class="person__last">Hartley</span></p>
      <p class="person__role">Director</p>
    </div>
    <span class="side-tab"></span>

    <address class="address">
      Suite 4.12, Tower 3<br>
      18 Harbourline Road<br>
      Riverside Park NSW 2150
    </address>
  </section>

  <section class="card card--back" aria-label="Business card back">
    <div class="back-field" role="img" aria-label="Repeating brand-mark pattern in blue tones"></div>
    <div class="back-brand">
      <span class="back-brand__dot"></span>
      <span class="back-brand__name">MRT Property</span>
    </div>
  </section>

</main>
</body>
</html>
```